Tech business card design

We need an amazing business card design for our new business 'Pexla' a marketing tech startup based in Sydney, Australia. We provide an online marketplace for businesses to search and buy advertising media, connect with service providers and learn more about marketing. We wish to communicate 'cool tech', reliability and professionalism and design based around our logo.

Target Market(s)

Business Owners

Contact Information for Business Card

Name
Position
Email Address
Website
Phone Number

Font styles to use
Other font styles liked:
• Avenir & Avenir Next

Colors

Designer to choose colors to be used in the design.

```html
<!DOCTYPE html>
<html lang="en">
<head>
<meta charset="utf-8">
<title>Pexla Business Card</title>
<link rel="stylesheet" href="https://fonts.googleapis.com/css2?family=Arimo:wght@400;700&display=swap">
<style>
  :root {
    --stage: #1e1e20;
    --card-white: #ffffff;
    --navy: #1b2350;
    --steel: #8a8b8f;
    --slate: #6d6e71;
    --ink: #2b2b2f;
    --rule: #9a9aa0;
  }
  * { box-sizing: border-box; margin: 0; padding: 0; }
  html, body {
    width: 1200px; height: 803px; overflow: hidden;
    background: var(--stage);
    font-family: "Arimo", Arial, sans-serif;
  }
  .stage {
    position: relative; width: 1200px; height: 803px;
    display: flex; align-items: center; justify-content: center; gap: 40px;
  }
  .card {
    position: relative; width: 540px; height: 310px; overflow: hidden;
    box-shadow: 0 12px 30px rgba(0,0,0,.5);
  }
  .card--front { background: var(--card-white); }
  .card--back {
    background: var(--slate);
    display: flex; align-items: center; justify-content: center;
  }
  .wave { position: absolute; inset: 0; width: 100%; height: 100%; }
  .brand-name {
    position: absolute; left: 40px; top: 120px;
    font-weight: 700; font-size: 82px; letter-spacing: -1px;
    color: var(--navy); line-height: 1;
  }
  .card--back .brand-name {
    position: static; font-size: 120px; color: var(--navy);
  }
  .contact {
    position: absolute; left: 330px; top: 26px;
    padding-left: 12px; border-left: 1px solid var(--rule);
    color: var(--ink); font-size: 12.5px; line-height: 1.35;
  }
  .contact__address { margin-bottom: 12px; }
  .contact__line { display: flex; align-items: center; gap: 5px; }
  .contact__line svg { width: 11px; height: 11px; flex: none; }
  .holder {
    position: absolute; right: 34px; top: 205px;
    color: var(--card-white); text-align: right; font-weight: 700;
  }
  .holder__name { font-size: 15px; letter-spacing: .5px; }
  .holder__role { font-size: 12.5px; margin-top: 2px; }
</style>
</head>
<body>
<main class="stage">
  <section class="card card--front">
    <svg class="wave" viewBox="0 0 540 310" preserveAspectRatio="none" aria-hidden="true">
      <path d="M0,262 C160,262 230,205 310,160 C380,122 440,168 540,168 L540,180 C440,182 390,138 320,176 C240,220 170,278 0,278 Z" fill="var(--steel)"/>
      <path d="M0,280 C170,280 240,222 320,180 C390,142 440,186 540,186 L540,310 L0,310 Z" fill="var(--navy)"/>
      <path d="M0,292 C180,292 260,240 340,200 C400,170 450,198 540,196" fill="none" stroke="var(--steel)" stroke-width="2"/>
      <path d="M0,300 C190,300 270,250 350,212" fill="none" stroke="var(--card-white)" stroke-width="2"/>
    </svg>
    <div class="brand-name">Pexla</div>
    <div class="contact">
      <p class="contact__address">Street Name, City Name<br>Zipcode:012345</p>
      <p class="contact__line">
        <svg viewBox="0 0 12 12"><path d="M2.5 1 L4.5 1 L5.3 3.5 L4 4.5 C4.7 6 6 7.3 7.5 8 L8.5 6.7 L11 7.5 L11 9.5 C11 10.3 10.3 11 9.5 11 C5 11 1 7 1 2.5 C1 1.7 1.7 1 2.5 1 Z" fill="var(--ink)"/></svg>
        012-345-6789
      </p>
      <p class="contact__line">
        <svg viewBox="0 0 12 12"><rect x="0.5" y="2" width="11" height="8" fill="none" stroke="var(--ink)"/><path d="M0.5 2 L6 7 L11.5 2" fill="none" stroke="var(--ink)"/></svg>
        info@pexla.com
      </p>
      <p class="contact__line">
        <svg viewBox="0 0 12 12"><circle cx="6" cy="6" r="5" fill="none" stroke="var(--ink)"/><ellipse cx="6" cy="6" rx="2.2" ry="5" fill="none" stroke="var(--ink)"/><path d="M1 6 H11" stroke="var(--ink)"/></svg>
        www.pexla.com
      </p>
    </div>
    <div class="holder">
      <p class="holder__name">JOHN SMITH</p>
      <p class="holder__role">Position</p>
    </div>
  </section>
  <section class="card card--back">
    <div class="brand-name">Pexla</div>
  </section>
</main>
</body>
</html>
```